Our companies name is The Gilded Ladle and we specialize in craft cupcakes, what I mean by that is that we bake our cupcakes with craft beer and other alcoholic drinks. We are trying to focus on being elegant but at the same time unpretentious. Since we are incorporating beer in our cupcakes we want the business card to have our logo in the front and our information in the back.

Once we select the best design we will provide the contact information to be added. Thank you.

Industry/Entity Type

Business

Font styles to use
Decorative
Script

Requirements
Must have
• Round corners
Should not have
• Square corners

```html
<!DOCTYPE html>
<html lang="en">
<head>
<meta charset="utf-8">
<title>The Gilded Ladle – Business Card</title>
<link rel="stylesheet" href="https://fonts.googleapis.com/css2?family=Michroma&display=swap">
<style>
  :root {
    --page-bg: #e6e6e6;
    --card-white: #ffffff;
    --card-shade: #e4e4e4;
    --teal: #84cfc3;
    --red: #e8242b;
    --band-gray: #dcdcdc;
    --ink: #3a3a3a;
    --ink-soft: #555555;
    --logo-dark: #1e1e1e;
    --on-teal: #ffffff;
  }
  html, body {
    margin: 0;
    padding: 0;
    width: 1200px;
    height: 900px;
    overflow: hidden;
    background: var(--page-bg);
    font-family: "Michroma", sans-serif;
  }
  .canvas {
    position: relative;
    width: 1200px;
    height: 900px;
  }
  .card {
    position: absolute;
    left: 300px;
    width: 600px;
    height: 343px;
    border-radius: 30px;
    overflow: hidden;
    background: radial-gradient(ellipse at 60% 40%, var(--card-white) 30%, var(--card-shade) 100%);
    box-shadow: 0 8px 22px rgba(0,0,0,0.18);
  }
  .card--back { top: 70px; }
  .card--front { top: 487px; }

  .card__wave {
    position: absolute;
    inset: 0;
    width: 100%;
    height: 100%;
  }

  .brand {
    position: absolute;
    display: flex;
    align-items: center;
    gap: 10px;
    color: var(--logo-dark);
    font-size: 15px;
    letter-spacing: 1px;
    text-transform: uppercase;
  }
  .brand__dot {
    width: 22px;
    height: 22px;
    border-radius: 50%;
    background: var(--red);
    flex: none;
  }
  .card--back .brand { left: 34px; top: 42px; }
  .card--front .brand {
    left: 50%;
    top: 50%;
    transform: translate(-50%, -50%);
    font-size: 24px;
    gap: 14px;
  }
  .card--front .brand__dot { width: 32px; height: 32px; }

  .person {
    position: absolute;
    left: 34px;
    top: 108px;
  }
  .person__name {
    margin: 0;
    font-size: 17px;
    color: var(--ink);
    letter-spacing: 2px;
    font-variant: small-caps;
  }
  .person__title {
    margin: 6px 0 0;
    font-size: 13px;
    color: var(--ink-soft);
    letter-spacing: 2px;
    font-variant: small-caps;
  }

  .contact {
    position: absolute;
    right: 34px;
    bottom: 26px;
    margin: 0;
    padding: 0;
    list-style: none;
    color: var(--on-teal);
    font-size: 10px;
    letter-spacing: 1px;
    line-height: 17px;
  }
  .contact__item {
    display: flex;
    align-items: flex-start;
    gap: 7px;
  }
  .contact__icon {
    width: 11px;
    height: 11px;
    margin-top: 3px;
    flex: none;
  }
  .contact__text--indent { padding-left: 18px; }
</style>
</head>
<body>
<main class="canvas">

  <section class="card card--back" aria-label="Back of business card">
    <svg class="card__wave" viewBox="0 0 600 343" preserveAspectRatio="none" aria-hidden="true">
      <path d="M0,118 C170,200 360,215 600,92 L600,343 L0,343 Z" fill="var(--band-gray)"/>
      <path d="M0,128 C170,212 360,226 600,104 L600,343 L0,343 Z" fill="var(--teal)"/>
      <path d="M0,112 C170,196 360,212 600,86" fill="none" stroke="var(--red)" stroke-width="4"/>
    </svg>

    <div class="brand">
      <span class="brand__dot"></span>
      <span class="brand__name">The Gilded Ladle</span>
    </div>

    <div class="person">
      <p class="person__name">Alan Mercer</p>
      <p class="person__title">Owner / C.E.O</p>
    </div>

    <ul class="contact">
      <li class="contact__item">
        <svg class="contact__icon" viewBox="0 0 12 12" aria-hidden="true"><path d="M6 0.5a4 4 0 0 0-4 4c0 3 4 7 4 7s4-4 4-7a4 4 0 0 0-4-4zm0 5.5a1.5 1.5 0 1 1 0-3 1.5 1.5 0 0 1 0 3z" fill="currentColor"/></svg>
        <span>Suite # 118, Elm Court,</span>
      </li>
      <li class="contact__item"><span class="contact__text--indent">NY 10458</span></li>
      <li class="contact__item">
        <svg class="contact__icon" viewBox="0 0 12 12" aria-hidden="true"><path d="M2.5 1l2 2.5-1 1.5c.8 1.6 1.9 2.7 3.5 3.5l1.5-1 2.5 2-1.2 1.5C5 10.5 1.5 7 1 2.2z" fill="currentColor"/></svg>
        <span>212-555-0147</span>
      </li>
      <li class="contact__item">
        <svg class="contact__icon" viewBox="0 0 12 12" aria-hidden="true"><rect x="3" y="0.5" width="6" height="11" rx="1.2" fill="currentColor"/></svg>
        <span>212-555-0193</span>
      </li>
      <li class="contact__item">
        <svg class="contact__icon" viewBox="0 0 12 12" aria-hidden="true"><rect x="1" y="3" width="10" height="7" rx="1" fill="currentColor"/><rect x="3" y="1" width="6" height="3" fill="currentColor"/></svg>
        <span>212-555-0128</span>
      </li>
      <li class="contact__item">
        <svg class="contact__icon" viewBox="0 0 12 12" aria-hidden="true"><rect x="0.5" y="2" width="11" height="8" rx="1" fill="currentColor"/><path d="M1 2.5l5 4 5-4" fill="none" stroke="var(--teal)" stroke-width="1"/></svg>
        <span>hello@gildedladle.com</span>
      </li>
      <li class="contact__item"><span class="contact__text--indent">www.gildedladle.com</span></li>
    </ul>
  </section>

  <section class="card card--front" aria-label="Front of business card">
    <div class="brand">
      <span class="brand__dot"></span>
      <span class="brand__name">The Gilded Ladle</span>
    </div>
  </section>

</main>
</body>
</html>
```